Radon Reduction & Mold Removal Website

I need you to set up a WordPress account for me and design a full width, professional-looking, mobile-responsive website for my business. We offer radon reduction and mold removal (two household environmental issues).
We have merged 2 companies and need a single website to promote both services (radon and mold). Here are the current websites from the 2 businesses that have merged:
RADON
http://plinth-airworks.com/
MOLD
http://quellbright-spores.net/
Once complete, I will need the login to the WordPress account so I have access to the site to make changes, additions, and modifications.
Target Market(s)
Home Owners
Industry/Entity Type
Home And Garden
Look and feel
Each slider illustrates characteristics of the customer's brand and the style your logo design should communicate.

```html
<!DOCTYPE html>
<html lang="en">
<head>
<meta charset="utf-8">
<title>Plinth Airworks — Radon Reduction &amp; Mold Removal</title>
<link href="https://fonts.googleapis.com/css2?family=Raleway:wght@400;500;600;700&family=Open+Sans:wght@400;600;700&display=swap" rel="stylesheet">
<style>
:root{
  --black:#0b0b0b;
  --green:#5cc31f;
  --green-dark:#3e9a12;
  --yellow:#f4f20a;
  --btn-yellow:#ffe600;
  --red:#d8201c;
  --ink:#2a2a2a;
  --muted:#666;
  --footer:#2b2b2b;
  --footer-bottom:#1f1f1f;
  --white:#fff;
}
*{box-sizing:border-box;margin:0;padding:0}
html,body{width:1200px;height:2894px;overflow:hidden;background:var(--white)}
body{font-family:"Open Sans",sans-serif;color:var(--ink);position:relative}
.abs{position:absolute}
h1,h2,h3,h4{font-family:"Raleway",sans-serif;font-weight:500}

/* header */
.topbar{left:0;top:0;width:1200px;height:88px;background:var(--black)}
.navband{left:0;top:88px;width:1200px;height:44px;background:linear-gradient(var(--green),var(--green-dark))}
.nav a{position:absolute;top:101px;color:#fff;font:600 14px "Open Sans",sans-serif;text-decoration:none;letter-spacing:.3px}
.brand{left:498px;top:20px;width:204px;height:144px;text-align:center}
.brand .tag{font:700 19px "Raleway",sans-serif;color:var(--green);line-height:22px}
.brand .tag.red{color:var(--red)}
.brand .box{margin:2px auto;width:200px;height:94px;background:var(--yellow);border-radius:6px;display:flex;align-items:center;justify-content:center;font:700 30px "Raleway",sans-serif;color:var(--black)}
.callus{left:944px;top:32px;color:var(--yellow);font:600 14px "Open Sans",sans-serif}
.phone{left:884px;top:52px;color:#fff;font:700 18px "Open Sans",sans-serif;display:flex;align-items:center;gap:6px}

/* hero */
.hero{left:0;top:132px;width:1200px;height:481px;background:linear-gradient(120deg,#cfc6b8 0%,#8d7c68 40%,#6b4a33 70%,#a88d70 100%)}
.quote{left:266px;top:266px;width:674px;height:191px;background:rgba(0,0,0,.72)}
.quote h2{position:absolute;top:20px;width:100%;text-align:center;color:#fff;font-size:22px;font-weight:500}
.field{position:absolute;width:148px;height:27px;background:#fff;border-radius:2px;font-size:10px;color:#777;padding:7px 8px}
.btn{position:absolute;height:32px;width:110px;font:700 14px "Open Sans",sans-serif;display:flex;align-items:center;justify-content:center;border-radius:2px}
.btn.submit{background:var(--btn-yellow);color:#222;left:228px;top:140px}
.btn.reset{background:var(--green);color:#fff;left:344px;top:140px}
.dots{left:554px;top:572px;display:flex;gap:6px}
.dots span{width:16px;height:16px;border-radius:50%;background:rgba(255,255,255,.55)}
.dots span:first-child{background:#fff}

/* radon intro */
.intro{left:150px;top:668px;width:900px;text-align:center}
.intro h1{font-size:27px;letter-spacing:.3px;margin-bottom:22px}
.intro p{font-size:11.5px;line-height:18px;color:var(--muted);margin-bottom:8px}

/* services band */
.services{left:0;top:903px;width:1200px;height:355px;background:linear-gradient(100deg,#5a4026 0%,#3c2d20 40%,#4f4a45 70%,#2e2a28 100%)}
.svc{position:absolute;top:960px;width:200px;text-align:center;color:#fff}
.svc .ico{width:98px;height:98px;border-radius:50%;background:var(--green);border:3px solid #fff;margin:0 auto 18px;display:flex;align-items:center;justify-content:center}
.svc h3{font-size:18px;font-weight:600;margin-bottom:6px}
.svc p{font-size:11px;line-height:15px;color:#ddd;height:48px}
.svc .more{display:inline-block;margin-top:14px;border:1.5px solid #fff;padding:6px 16px;font:600 10px "Open Sans",sans-serif}

/* news */
.news{left:178px;top:1340px;width:450px}
.news h2{font-size:24px;font-weight:500;letter-spacing:.5px}
.news h3{font-size:16px;font-weight:700;margin:6px 0 16px}
.news p{font-size:11px;line-height:18px;color:var(--muted);margin-bottom:12px}
.video{left:662px;top:1323px;width:358px;height:208px;background:linear-gradient(135deg,#3a3a3a,#111 60%,#5b5b5b)}
.play{left:812px;top:1398px}
.rule{left:0;top:1606px;width:1200px;height:1px;background:#e3e3e3}

/* mold cards */
.mold{left:0;top:1607px;width:1200px;height:328px;background:linear-gradient(#fff,#e9e9e9)}
.card{position:absolute;top:1664px;width:268px}
.card .ph{height:126px;background:linear-gradient(135deg,#e8e0d4,#b7a089)}
.card h4{font-size:16px;font-weight:600;margin:12px 0 8px}
.card p{font-size:11px;line-height:18px;color:var(--muted)}

/* testimonials */
.testi{left:0;top:1935px;width:1200px;height:264px;background:var(--btn-yellow)}
.testi h2{position:absolute;top:62px;width:100%;text-align:center;font-size:26px;font-weight:500}
.testi blockquote{position:absolute;left:330px;top:117px;width:540px;text-align:center;font:italic 11px/18px "Open Sans",sans-serif;color:#333}
.testi .by{position:absolute;top:178px;width:100%;text-align:center;font-size:11px;color:#333}
.qmark{font:700 34px Georgia,serif;color:#333;position:absolute}

/* gallery */
.gallery{left:0;top:2199px;width:1200px;height:390px;background:linear-gradient(120deg,#e2ded8,#c9bfb2 50%,#e6e2dc)}
.gallery h2{position:absolute;top:42px;width:100%;text-align:center;font-size:23px;font-weight:600}
.tile{position:absolute;width:125px;height:102px}

/* footer */
.footer{left:0;top:2589px;width:1200px;height:241px;background:var(--footer)}
.fcol{position:absolute;top:2624px;color:#ddd}
.fcol h4{font-size:21px;font-weight:400;color:#eee;margin-bottom:10px}
.fcol li{list-style:none;font-size:12px;line-height:25px}
.fcol p{font-size:12px;line-height:25px}
.email{width:240px;height:30px;background:#eee;border-radius:2px;margin-top:8px;font-size:11px;color:#777;padding:8px 10px}
.sub{width:114px;height:32px;background:var(--green);color:#fff;font-size:12px;font-weight:600;display:flex;align-items:center;justify-content:center;margin-top:10px}
.fbottom{left:0;top:2830px;width:1200px;height:64px;background:var(--footer-bottom);border-top:1px solid #333}
.copy{left:174px;top:2857px;font-size:10px;color:#aaa}
.social{left:930px;top:2854px;display:flex;gap:6px}
.social span{width:16px;height:16px;background:#eee;border-radius:2px}
</style>
</head>
<body>

<div class="abs topbar"></div>
<div class="abs navband"></div>
<nav class="nav">
  <a style="left:190px" href="#">HOME</a>
  <a style="left:268px" href="#">ABOUT US</a>
  <a style="left:374px" href="#">SERVICES</a>
  <a style="left:736px" href="#">PRODUCTS</a>
  <a style="left:846px" href="#">GET A QUOTE</a>
  <a style="left:970px" href="#">CONTACT</a>
</nav>
<div class="abs brand">
  <div class="tag">Mold Removal</div>
  <div class="box">Plinth Airworks</div>
  <div class="tag red">Radon Reduction</div>
</div>
<div class="abs callus">Call Us Now</div>
<div class="abs phone">
  <svg width="14" height="14" viewBox="0 0 24 24"><path fill="#f4f20a" d="M6.6 10.8a15 15 0 0 0 6.6 6.6l2.2-2.2c.3-.3.7-.4 1-.2 1.1.4 2.3.6 3.6.6.6 0 1 .4 1 1V20c0 .6-.4 1-1 1A17 17 0 0 1 3 4c0-.6.4-1 1-1h3.5c.6 0 1 .4 1 1 0 1.3.2 2.5.6 3.6.1.3 0 .7-.2 1z"/></svg>
  1-800-555-0142
</div>

<section class="abs hero" role="img" aria-label="Photo of two workers tearing out a damaged wooden floor"></section>
<form class="abs quote">
  <h2>REQUEST A QUOTE</h2>
  <div class="field" style="left:32px;top:64px">Your Name</div>
  <div class="field" style="left:190px;top:64px">Phone no.</div>
  <div class="field" style="left:348px;top:64px">Email address</div>
  <div class="field" style="left:506px;top:64px">City/State</div>
  <div class="field" style="left:32px;top:100px">Zip Code</div>
  <div class="field" style="left:190px;top:100px">Mold Location ▾</div>
  <div class="field" style="left:348px;top:100px">Inspection Report ▾</div>
  <div class="field" style="left:506px;top:100px">Notes</div>
  <div class="btn submit">SUBMIT</div>
  <div class="btn reset">RESET</div>
</form>
<div class="abs dots"><span></span><span></span><span></span><span></span></div>

<section class="abs intro">
  <h1>RADON MITIGATION AND RADON GAS REMOVAL</h1>
  <p>High levels of radon have been found in every state across America. Radon Mitigation and radon testing have become more prevalent in the past few years in residential, commercial and real-estate environments with the real-estate market showing the biggest growth due to some state and local real-estate regulations mandating the testing and mitigation of radon in homes on the market.</p>
  <p>Radon Mitigation and the removal of radon gas are generally accomplished by removing radon from below the house or building by way of fan suction and removing the radon gas safely through a pipe that extends past the roof line of the structure where the radon gas is released and effectively removed</p>
</section>

<section class="abs services" role="img" aria-label="Dimmed photo of a worker installing equipment in a home"></section>
<div class="svc" style="left:160px">
  <div class="ico"><svg width="50" height="50" viewBox="0 0 24 24"><path fill="#fff" d="M12 3 2 11h3v9h6v-6h2v6h6v-9h3z"/></svg></div>
  <h3>Residential Service</h3>
  <p>Safe testing and radon reduction for family homes of every size and age</p>
  <span class="more">READ MORE</span>
</div>
<div class="svc" style="left:388px">
  <div class="ico"><svg width="46" height="46" viewBox="0 0 24 24"><path fill="#fff" d="M4 21V5h9v16zm2-14v2h2V7zm3 0v2h2V7zM6 11v2h2v-2zm3 0v2h2v-2zM6 15v2h2v-2zm3 0v2h2v-2zm5 6V9h6v12z"/></svg></div>
  <h3>Commerical Service</h3>
  <p>Mitigation plans for offices, schools and rental buildings done on schedule</p>
  <span class="more">READ MORE</span>
</div>
<div class="svc" style="left:614px">
  <div class="ico"><svg width="48" height="48" viewBox="0 0 24 24"><path fill="#fff" d="M3 9 12 3l9 6-1 1.5-8-5.3-8 5.3zm3 2h12v9H6zm2 2v2h3v-2zm5 0v2h3v-2zm-5 3v2h3v-2zm5 0v2h3v-2z"/></svg></div>
  <h3>Real Estate Service</h3>
  <p>Fast inspections and clear reports to keep your home sale moving along</p>
  <span class="more">READ MORE</span>
</div>
<div class="svc" style="left:840px">
  <div class="ico"><svg width="44" height="44" viewBox="0 0 24 24"><path fill="none" stroke="#fff" stroke-width="2" d="M3 11c0-4 4-7 8-7s8 3 8 7-4 7-8 7c-1 0-2 0-3-.4L4 20l1-3.5C3.7 15 3 13 3 11z"/><path fill="none" stroke="#fff" stroke-width="2" d="M8 11h6"/></svg></div>
  <h3>Get a Quote</h3>
  <p>Tell us about your property and receive a free, no pressure estimate today</p>
  <span class="more">READ MORE</span>
</div>

<article class="abs news">
  <h2>NONSMOKING WOMAN BELIEVES</h2>
  <h3>RADON CAUSED HER LUNG CANCER</h3>
  <p>BELLVILLE, OH (WKRV) - It is the number one cause of lung cancer in nonsmokers and it could be in your house. One woman believes radon in her home made her sick.</p>
  <p>Warning about radon levels in homes One thing becomes quickly clear when a radon reduction system is being installed, everything must be tightly sealed for it to work properly, according to removal expert Dale Fenwick, who installed a system in Janet and Rob Ellery's home.</p>
</article>
<div class="abs video" role="img" aria-label="Video still of hands fitting a white vent pipe"></div>
<svg class="abs play" width="56" height="56" viewBox="0 0 56 56"><circle cx="28" cy="28" r="26" fill="#fff"/><path d="M22 17v22l18-11z" fill="#111"/></svg>
<div class="abs rule"></div>

<section class="abs mold"></section>
<div class="card" style="left:170px">
  <div class="ph" role="img" aria-label="Photo of a technician treating a wall"></div>
  <h4>Residential Mold Removal</h4>
  <p>Assessment of the situation is the first step in the mold removal process. This allows our professionals to document all mold</p>
</div>
<div class="card" style="left:463px">
  <div class="ph" role="img" aria-label="Photo of water damaged basement drywall"></div>
  <h4>Basement Mold</h4>
  <p>Assessment of the situation is the first step in the mold removal process. This allows our professionals to document all mold</p>
</div>
<div class="card" style="left:754px">
  <div class="ph" role="img" aria-label="Photo of a worker removing flooring"></div>
  <h4>Commercial Mold Remediation</h4>
  <p>Assessment of the situation is the first step in the mold removal process. This allows our professionals to document all mold</p>
</div>

<section class="abs testi">
  <h2>TESTIMONIALS</h2>
  <svg style="position:absolute;left:242px;top:96px" width="28" height="64" viewBox="0 0 28 64"><path d="M26 2 2 32l24 30" fill="none" stroke="#555" stroke-width="1.5"/></svg>
  <svg style="position:absolute;left:930px;top:96px" width="28" height="64" viewBox="0 0 28 64"><path d="M2 2l24 30L2 62" fill="none" stroke="#555" stroke-width="1.5"/></svg>
  <span class="qmark" style="left:310px;top:100px">“</span>
  <blockquote>Morbi diam mauris viverra in gravida eu mattis in ante Morbi eget arcu Morbi porta libero id ullamcorper nonummy nibh ligula pulvinar metus eget consectetuer augue nisi quis lacus Ut ac mi quis lacus mollis aliquam Curabitur iaculis tempus eros Curabitur vel mi sit amet Mauris vel lacus vitae felis</blockquote>
  <span class="qmark" style="left:812px;top:142px">”</span>
  <div class="by">By Author Name, City Location</div>
</section>

<section class="abs gallery" role="img" aria-label="Faded photo of workers renovating a room">
  <h2>OUR GALLERY</h2>
</section>
<div class="tile" style="left:187px;top:2296px;background:linear-gradient(135deg,#7d8a94,#3e4a52)" role="img" aria-label="Gallery photo: window exterior"></div>
<div class="tile" style="left:326px;top:2296px;background:linear-gradient(135deg,#4a3a2a,#b9a06a)" role="img" aria-label="Gallery photo: round vent fan"></div>
<div class="tile" style="left:465px;top:2296px;background:linear-gradient(135deg,#c7734a,#8a4a2c)" role="img" aria-label="Gallery photo: pipe on brick wall"></div>
<div class="tile" style="left:604px;top:2296px;background:linear-gradient(135deg,#8d9470,#5e6a4a)" role="img" aria-label="Gallery photo: exterior vent pipe"></div>
<div class="tile" style="left:743px;top:2296px;background:linear-gradient(135deg,#e6e6e6,#9a9a9a)" role="img" aria-label="Gallery photo: radon fan unit"></div>
<div class="tile" style="left:882px;top:2296px;background:linear-gradient(135deg,#d6d6d6,#6f6f6f)" role="img" aria-label="Gallery photo: sump pipe system"></div>
<div class="tile" style="left:187px;top:2415px;background:linear-gradient(135deg,#d8d4cc,#8e8a80)" role="img" aria-label="Gallery photo: basement pipe run"></div>
<div class="tile" style="left:326px;top:2415px;background:linear-gradient(135deg,#6f8fb0,#3c4d60)" role="img" aria-label="Gallery photo: house corner and sky"></div>
<div class="tile" style="left:465px;top:2415px;background:linear-gradient(135deg,#b58a5a,#6e4e30)" role="img" aria-label="Gallery photo: siding with pipe"></div>
<div class="tile" style="left:604px;top:2415px;background:linear-gradient(135deg,#c9bfa8,#8d8068)" role="img" aria-label="Gallery photo: stucco wall pipe"></div>
<div class="tile" style="left:743px;top:2415px;background:linear-gradient(135deg,#c0703c,#e9e4dc)" role="img" aria-label="Gallery photo: fan on wood siding"></div>
<div class="tile" style="left:882px;top:2415px;background:linear-gradient(135deg,#4f86c6,#c9b48a)" role="img" aria-label="Gallery photo: roof line vent"></div>

<footer class="abs footer"></footer>
<div class="fcol" style="left:176px">
  <h4>About Us</h4>
  <ul><li>Our Vision</li><li>About Us</li><li>Testimonials</li><li>Clients</li><li>Gallery</li></ul>
</div>
<div class="fcol" style="left:348px">
  <h4>Services</h4>
  <ul><li>Class aptent taciti</li><li>Sociosqu ad litora</li><li>Torquent per</li><li>Conubia nostra</li><li>Per inceptos</li></ul>
</div>
<div class="fcol" style="left:548px">
  <h4>Newsletter Sign Up</h4>
  <p>Please sign Up here for latest news.</p>
  <div class="email">Email address</div>
  <div class="sub">SUBSCRIBE</div>
</div>
<div class="fcol" style="left:852px">
  <h4>Contact Us</h4>
  <p>Office: 1-800-555-0187</p>
  <p>Email : hello@plinthairworks.com</p>
  <p>Mon - Fri : 7am - 8pm</p>
  <p>Sat : 8am - 3pm</p>
</div>
<div class="abs fbottom"></div>
<div class="abs copy">© 2015 Company Name. All right reserved. Term of Use</div>
<div class="abs social"><span></span><span></span><span></span></div>

</body>
</html>
```